Christmas Collection Candle Label Design

Looking to update our existing Christmas Candle Collection labels. Labels should reflect the overall feel of our brand- www.kelvanoro.ca
Want to include some color elements. Holiday colors added into design but more muted/ earthy tones not vibrant colors . Metallic elements and line art botanical illustration. Fonts should be more align to brand
Scents
Holiday Tree
Candy Cane
Sugar and Spice
Joyeaux Noel

```html
<!DOCTYPE html>
<html lang="en">
<head>
<meta charset="utf-8">
<title>Candy Cane – Christmas Collection Label</title>
<link rel="stylesheet" href="https://fonts.googleapis.com/css2?family=Lato:wght@300;400&family=Noto+Serif:wght@700&display=swap">
<style>
  :root {
    --backdrop: #cfe2e3;
    --wrap-white: #f6f6f6;
    --wrap-edge: #dcdcdc;
    --panel-top: #b8c8c6;
    --panel-bottom: #9fb0af;
    --art-light: rgba(240, 244, 242, 0.55);
    --art-mid: rgba(226, 233, 231, 0.35);
    --ink: #222222;
    --ink-soft: #2c2c2c;
  }
  * { margin: 0; padding: 0; box-sizing: border-box; }
  html, body {
    width: 1200px;
    height: 771px;
    overflow: hidden;
    background: var(--backdrop);
  }
  .canvas {
    position: relative;
    width: 1200px;
    height: 771px;
    background: var(--backdrop);
  }
  .label-wrap {
    position: absolute;
    left: 280px;
    top: 135px;
    width: 640px;
    height: 500px;
    background: linear-gradient(90deg, var(--wrap-white), var(--wrap-edge));
  }
  .label-panel {
    position: absolute;
    left: 60px;
    top: 0;
    width: 520px;
    height: 500px;
    background: linear-gradient(160deg, var(--panel-top), var(--panel-bottom));
    overflow: hidden;
  }
  .botanical-art {
    position: absolute;
    left: 18px;
    top: 0;
    width: 502px;
    height: 500px;
    background:
      radial-gradient(ellipse 90px 140px at 42% 30%, var(--art-light), transparent 70%),
      radial-gradient(ellipse 80px 150px at 88% 38%, var(--art-light), transparent 70%),
      radial-gradient(ellipse 150px 60px at 62% 48%, var(--art-mid), transparent 70%),
      radial-gradient(ellipse 70px 110px at 32% 62%, var(--art-mid), transparent 70%),
      radial-gradient(ellipse 70px 90px at 10% 86%, var(--art-light), transparent 70%),
      radial-gradient(ellipse 60px 80px at 88% 78%, var(--art-mid), transparent 70%);
  }
  .brand {
    position: absolute;
    top: 34px;
    left: 0;
    width: 100%;
    text-align: center;
    color: var(--ink-soft);
    font-family: "Lato", sans-serif;
  }
  .brand-dot {
    display: block;
    width: 5px;
    height: 5px;
    margin: 0 auto 6px;
    border-radius: 50%;
    background: var(--ink-soft);
  }
  .brand-name {
    font-size: 22px;
    font-weight: 400;
    letter-spacing: 0.5px;
    line-height: 1;
  }
  .brand-tagline {
    margin-top: 4px;
    font-size: 6px;
    letter-spacing: 1.6px;
    text-transform: uppercase;
  }
  .scent-note {
    position: absolute;
    top: 272px;
    right: 104px;
    font-family: "Lato", sans-serif;
    font-size: 10px;
    color: var(--ink);
  }
  .scent-name {
    position: absolute;
    top: 286px;
    right: 100px;
    text-align: right;
    font-family: "Noto Serif", serif;
    font-weight: 700;
    font-size: 58px;
    line-height: 62px;
    color: var(--ink);
  }
  .details {
    position: absolute;
    left: 120px;
    top: 414px;
    width: 292px;
    font-family: "Lato", sans-serif;
    font-weight: 300;
    font-size: 18px;
    color: var(--ink);
    border-top: 1px solid var(--ink);
  }
  .details-row {
    display: flex;
    height: 30px;
    border-bottom: 1px solid var(--ink);
  }
  .details-cell {
    display: flex;
    align-items: center;
    justify-content: center;
    white-space: nowrap;
  }
  .row-size .details-cell:first-child { width: 97px; border-right: 1px solid var(--ink); }
  .row-origin .details-cell:first-child { width: 133px; border-right: 1px solid var(--ink); }
  .details-cell:last-child { flex: 1; }
</style>
</head>
<body>
<main class="canvas">
  <section class="label-wrap">
    <div class="label-panel">
      <div class="botanical-art" role="img" aria-label="Pale white line-art botanical illustration of large flowing petals and stems spreading across the label"></div>

      <header class="brand">
        <span class="brand-dot"></span>
        <div class="brand-name">KELVANORO</div>
        <div class="brand-tagline">Pure plant based scents</div>
      </header>

      <p class="scent-note">made with plant based botanical</p>
      <h1 class="scent-name">CANDY<br>CANE</h1>

      <div class="details">
        <div class="details-row row-size">
          <span class="details-cell">13 oz</span>
          <span class="details-cell">Christmas Collection</span>
        </div>
        <div class="details-row row-origin">
          <span class="details-cell">kelvanoro</span>
          <span class="details-cell">made in canada</span>
        </div>
      </div>
    </div>
  </section>
</main>
</body>
</html>
```